New Business Card Design Project

Need a design that will create an impact / strong impression towards our clients for our business. We are in the lighting business and we do lighting retrofits for large commercial to industrial clientele.

Target Market(s)

Lighting Industry

Industry/Entity Type

Business

Font styles to use
Other font styles liked:
• we would like to use the font on our logo, not sure what it is though..

Requirements
Must have
• Our logo.
Nice to have
• We are open to suggestions that have to do with lighting.

```html
<!DOCTYPE html>
<html lang="en">
<head>
<meta charset="utf-8">
<title>Lumenfield Retrofit Co. — Business Card</title>
<link href="https://fonts.googleapis.com/css2?family=Roboto:wght@400;500;700&family=Roboto+Condensed:wght@500&display=swap" rel="stylesheet">
<style>
  :root {
    --backdrop: #5a4939;
    --card-white: #f2f2f2;
    --green-light: #64bf52;
    --green-mid: #0a7e39;
    --green-deep: #113510;
    --ink-green: #0f4d1f;
    --text-white: #ffffff;
  }
  * { margin: 0; padding: 0; box-sizing: border-box; }
  html, body { width: 1200px; height: 960px; overflow: hidden; }
  body {
    background: var(--backdrop);
    font-family: "Roboto", Arial, sans-serif;
    position: relative;
  }
  .card {
    position: absolute;
    width: 600px;
    height: 343px;
    box-shadow: 0 2px 4px rgba(0,0,0,0.35);
  }
  .card-front { left: 314px; top: 113px; background: var(--card-white); }
  .card-back { left: 312px; top: 472px; background: var(--green-deep); }

  .brand {
    position: absolute;
    left: 0; right: 0; top: 72px;
    display: flex;
    justify-content: center;
    align-items: center;
    gap: 12px;
  }
  .brand-mark { width: 22px; height: 22px; background: var(--green-light); }
  .brand-name {
    font-family: "Roboto", Arial, sans-serif;
    font-weight: 700;
    font-size: 32px;
    letter-spacing: 1px;
    color: var(--ink-green);
  }

  .info-band {
    position: absolute;
    left: 0; top: 200px;
    width: 600px; height: 123px;
    display: flex;
  }
  .identity {
    width: 299px;
    background: var(--green-light);
    color: var(--text-white);
    padding: 20px 0 0 36px;
  }
  .band-divider { width: 2px; background: var(--card-white); }
  .contact {
    flex: 1;
    background: var(--green-mid);
    color: var(--text-white);
    padding: 25px 38px 0 0;
  }
  .person-name {
    font-family: "Roboto Condensed", Arial, sans-serif;
    font-weight: 500;
    font-size: 23px;
    line-height: 25px;
  }
  .person-title {
    font-family: "Roboto Condensed", Arial, sans-serif;
    font-weight: 500;
    font-size: 16px;
    line-height: 18px;
  }
  .address { font-size: 14.5px; line-height: 19px; margin-top: 2px; }
  .contact-list { list-style: none; }
  .contact-list li {
    display: flex;
    justify-content: flex-end;
    align-items: center;
    gap: 6px;
    font-size: 14.5px;
    line-height: 19.5px;
  }
  .contact-list svg { width: 13px; height: 13px; fill: var(--green-light); }

  .back-brand {
    position: absolute;
    left: 0; right: 0; top: 140px;
    display: flex;
    justify-content: center;
    align-items: center;
    gap: 14px;
  }
  .back-brand .brand-mark { width: 26px; height: 26px; }
  .back-brand .brand-name { color: var(--text-white); font-size: 38px; }
  .website {
    position: absolute;
    left: 0; right: 0; top: 282px;
    text-align: center;
    color: var(--text-white);
    font-size: 14px;
    letter-spacing: 3px;
  }
</style>
</head>
<body>
  <section class="card card-front">
    <div class="brand">
      <span class="brand-mark"></span>
      <span class="brand-name">LUMENFIELD RETROFIT CO.</span>
    </div>
    <div class="info-band">
      <div class="identity">
        <p class="person-name">DANIEL REYES</p>
        <p class="person-title">CEO/FOUNDER</p>
        <p class="address">1420 Harbor View Road<br>Anchorage, Alaska 99501</p>
      </div>
      <div class="band-divider"></div>
      <div class="contact">
        <ul class="contact-list">
          <li>555 014 2238
            <svg viewBox="0 0 16 16" aria-hidden="true"><path d="M3.5 1l2.5 3-1.5 2c1 2 3 4 5 5l2-1.5 3 2.5-1.5 2.5C7.5 15 1 8.5 1 2.5z"/></svg>
          </li>
          <li>555 017 6493
            <svg viewBox="0 0 16 16" aria-hidden="true"><path d="M4 0h8v16H4zM5.5 2v10h5V2zM7 13.2h2v1.3H7z" fill-rule="evenodd"/></svg>
          </li>
          <li>555 019 8812
            <svg viewBox="0 0 16 16" aria-hidden="true"><path d="M4 1h8v4H4zM1 6h14v6h-3v3H4v-3H1zM5 10v4h6v-4z" fill-rule="evenodd"/></svg>
          </li>
          <li>daniel@lumenfield.com
            <svg viewBox="0 0 16 16" aria-hidden="true"><path d="M1 3h14v10H1zM2 4l6 5 6-5z" fill-rule="evenodd"/></svg>
          </li>
        </ul>
      </div>
    </div>
  </section>

  <section class="card card-back">
    <div class="back-brand">
      <span class="brand-mark"></span>
      <span class="brand-name">LUMENFIELD</span>
    </div>
    <p class="website">www.lumenfieldretrofit.com</p>
  </section>
</body>
</html>
```